New Business Card Design Project

We are a spa looking to create a professional elegant business card for a spa mainly black and white with a splash of lime green. This card will be two sided - the front side will have an image, the logo, and the spa's information - the back side will have a promotion for new customers - NEW CUSTOMERS $20 OFF

Look and feel: chic, modern, and spa-ish.
Information to be included:
Therapist Name
Therapist specialty
Address: 4719 Marlowe Ave, Beverly Hills CA 90211
Phone: (310) 482-3917

Let me know if you have any questions!

Thank you

```html
<!DOCTYPE html>
<html lang="en">
<head>
<meta charset="utf-8">
<title>Solace Day Spa — Business Card</title>
<link rel="stylesheet" href="https://fonts.googleapis.com/css2?family=Exo+2:wght@400;600;700&display=swap">
<style>
  :root {
    --lime: #93d40f;
    --ink: #0b0b0b;
    --paper: #ffffff;
    --grey: #4a4a4a;
    --backdrop: #e9e6e1;
  }
  * { box-sizing: border-box; margin: 0; padding: 0; }
  html, body { width: 1200px; height: 970px; overflow: hidden; }
  body {
    background: var(--backdrop);
    font-family: "Exo 2", sans-serif;
    position: relative;
  }
  .card {
    position: absolute;
    left: 220px;
    width: 760px;
    height: 434px;
    background: var(--paper);
    overflow: hidden;
    box-shadow: 0 10px 28px rgba(0,0,0,.18);
  }
  .card--back { top: 40px; }
  .card--front { top: 496px; }
  .card__art { position: absolute; inset: 0; }

  .brand {
    position: absolute;
    display: flex;
    align-items: center;
    gap: 10px;
    color: var(--ink);
    font-weight: 600;
    letter-spacing: .12em;
    text-transform: uppercase;
    white-space: nowrap;
  }
  .brand__dot {
    width: 16px; height: 16px;
    border-radius: 50%;
    background: var(--ink);
    flex: none;
  }
  .card--back .brand { right: 60px; top: 70px; font-size: 24px; }
  .card--front .brand { left: 60px; top: 160px; font-size: 18px; }

  .promo {
    position: absolute;
    right: 60px;
    top: 318px;
    text-align: right;
    text-transform: uppercase;
    line-height: 1;
  }
  .promo__lead {
    color: var(--ink);
    font-weight: 600;
    font-size: 20px;
    letter-spacing: .14em;
  }
  .promo__offer {
    color: var(--lime);
    font-weight: 700;
    font-size: 46px;
    letter-spacing: .04em;
    margin-top: 8px;
  }

  .edge-lines {
    position: absolute;
    background: repeating-linear-gradient(90deg, var(--lime) 0 1px, transparent 1px 5px);
    opacity: .8;
  }
  .edge-lines--bottom { left: 0; right: 0; bottom: 0; height: 10px; }
  .edge-lines--right { top: 0; bottom: 0; right: 0; width: 10px;
    background: repeating-linear-gradient(0deg, var(--lime) 0 1px, transparent 1px 5px); }

  .identity {
    position: absolute;
    left: 60px;
    top: 270px;
    width: 240px;
  }
  .identity__name {
    color: var(--lime);
    font-weight: 700;
    font-size: 32px;
    letter-spacing: .04em;
    text-transform: uppercase;
    white-space: nowrap;
  }
  .identity__specialty {
    color: var(--grey);
    font-size: 17px;
    letter-spacing: .1em;
    text-transform: uppercase;
    margin-top: 4px;
    white-space: nowrap;
  }
  .divider {
    position: absolute;
    left: 318px;
    top: 150px;
    width: 3px;
    height: 178px;
    background: var(--lime);
  }
  .contacts {
    position: absolute;
    left: 342px;
    top: 146px;
    list-style: none;
    color: var(--grey);
    font-size: 16px;
  }
  .contacts li {
    display: flex;
    align-items: center;
    gap: 12px;
    height: 37px;
    white-space: nowrap;
  }
  .contacts svg { width: 22px; height: 22px; flex: none; }
  .accent-bar { position: absolute; right: 0; bottom: 60px; }
</style>
</head>
<body>

<section class="card card--back" aria-label="Card back">
  <svg class="card__art" viewBox="0 0 760 434" aria-hidden="true">
    <polygon points="0,0 150,0 0,30" fill="#0b0b0b"/>
    <polygon points="0,270 560,150 760,150 760,160 0,330" fill="#93d40f"/>
    <polygon points="0,330 760,160 760,228 0,400" fill="#0b0b0b"/>
  </svg>
  <div class="brand"><span class="brand__dot"></span>Solace Day Spa</div>
  <div class="promo">
    <p class="promo__lead">New Customers</p>
    <p class="promo__offer">$20 Off</p>
  </div>
</section>

<section class="card card--front" aria-label="Card front">
  <div class="brand"><span class="brand__dot"></span>Solace Day Spa</div>

  <div class="identity">
    <p class="identity__name">Elena Marsh</p>
    <p class="identity__specialty">Massage Therapist</p>
  </div>

  <div class="divider"></div>

  <ul class="contacts">
    <li>
      <svg viewBox="0 0 22 22"><circle cx="11" cy="11" r="11" fill="#93d40f"/><path d="M7.5 6c1 0 1.6 2 1.3 2.6l-.8.9c.7 1.6 2 2.9 3.6 3.6l.9-.8c.6-.3 2.6.3 2.6 1.3 0 1-.9 2-2 2C9.4 15.6 6.4 12.6 6 8c0-1.1 1-2 1.5-2z" fill="#fff"/></svg>
      (310) 482-3917
    </li>
    <li>
      <svg viewBox="0 0 22 22"><circle cx="11" cy="11" r="11" fill="#93d40f"/><rect x="7.5" y="5" width="7" height="12" rx="1.3" fill="#fff"/><rect x="8.7" y="6.5" width="4.6" height="7.5" fill="#93d40f"/></svg>
      (310) 482-3920
    </li>
    <li>
      <svg viewBox="0 0 22 22"><circle cx="11" cy="11" r="11" fill="#93d40f"/><path d="M11 4.5a4.3 4.3 0 0 0-4.3 4.3c0 3.2 4.3 8.2 4.3 8.2s4.3-5 4.3-8.2A4.3 4.3 0 0 0 11 4.5z" fill="#fff"/><circle cx="11" cy="8.8" r="1.6" fill="#93d40f"/></svg>
      4719 Marlowe Ave, Beverly Hills CA 90211
    </li>
    <li>
      <svg viewBox="0 0 22 22"><circle cx="11" cy="11" r="11" fill="#93d40f"/><rect x="5.5" y="7" width="11" height="8" fill="#fff"/><path d="M5.5 7l5.5 4.5L16.5 7" fill="none" stroke="#93d40f" stroke-width="1.2"/></svg>
      hello@solacedayspa.com
    </li>
    <li>
      <svg viewBox="0 0 22 22"><circle cx="11" cy="11" r="11" fill="#93d40f"/><circle cx="11" cy="11" r="5.5" fill="none" stroke="#fff" stroke-width="1.4"/><path d="M5.5 11h11M11 5.5c-2.5 3-2.5 8 0 11M11 5.5c2.5 3 2.5 8 0 11" fill="none" stroke="#fff" stroke-width="1.1"/></svg>
      www.solacedayspa.com
    </li>
  </ul>

  <svg class="accent-bar" width="190" height="52" viewBox="0 0 190 52" aria-hidden="true">
    <polygon points="24,0 190,0 190,52 0,52" fill="#0b0b0b"/>
  </svg>

  <div class="edge-lines edge-lines--bottom"></div>
  <div class="edge-lines edge-lines--right"></div>
</section>

</body>
</html>
```